Elegant Business Card for Technology Company

Client is a supplier of innovative industrial communications and automation equipment since 2002. This contest is to gather fresh ideas for a redesign of the existing business card. Client is looking for design that best communicates tagline "Industrial Networking and Computing Specialist".

Design submissions should look modern, clean, elegant and professional. It should not be cluttered. Use white as the primary colour. Orange and black as secondary colour. Refer to jpeg File 1 on the current design.

Fonts used by Client used include Arial Regular, Arial Black, Roboto Regular, Roboto Black and Lato.

The winning design will be sent for offset printing using super white 250gsm artcard paper (open for suggestions).

Target Market(s)

System Engineers, Project Managers, Purchasing Managers from companies providing engineering services for Smart Cities.

Industry/Entity Type

Information Technology

Contact Information for Business Card

Refer to PDF File 3 for Business Card Details. Priority of short contact information would be as follows Name > Job Title > Email > Mobile > Web > Tel > Fax > Business Address >UEN (UEN represents company registration number)

Font styles to use
Sans Serif

Colors
ffffff
f37122
000000
5c5c5c

Requirements
Must have
• Refer to AI File 2 (Company Logo) & PDF File 3 (Information on Namecard)
Should not have
• No QR codes
• No Social Media Icons
• Do not create full Black or Orange colour background

```html
<!DOCTYPE html>
<html lang="en">
<head>
<meta charset="utf-8">
<title>Orvane Business Card</title>
<link rel="stylesheet" href="https://fonts.googleapis.com/css2?family=Roboto:wght@400;500;700;900&display=swap">
<style>
  :root {
    --white: #ffffff;
    --orange: #f37122;
    --black: #000000;
    --grey: #5c5c5c;
    --stage: #e6e6e6;
    --card-w: 600px;
    --card-h: 343px;
  }
  * { box-sizing: border-box; margin: 0; padding: 0; }
  html, body { width: 1200px; height: 900px; overflow: hidden; }
  body {
    background: var(--stage);
    font-family: "Roboto", Arial, sans-serif;
    color: var(--black);
    display: flex;
    flex-direction: column;
    align-items: center;
    justify-content: center;
    gap: 60px;
  }
  .card {
    position: relative;
    width: var(--card-w);
    height: var(--card-h);
    background: var(--white);
    border-radius: 22px;
    overflow: hidden;
    box-shadow: 0 6px 18px rgba(0,0,0,0.18);
  }

  /* brand lockup */
  .brand {
    display: flex;
    align-items: center;
    gap: 12px;
  }
  .brand-dot {
    width: 34px; height: 34px;
    border-radius: 50%;
    background: var(--orange);
  }
  .brand-name {
    font-weight: 900;
    font-size: 44px;
    letter-spacing: 1px;
    color: var(--black);
    line-height: 1;
  }

  /* front */
  .card-front .brand {
    position: absolute;
    top: 34px;
    left: 232px;
  }
  .front-rule-top {
    position: absolute;
    top: 92px;
    left: 470px;
    width: 110px;
    height: 1.5px;
    background: var(--orange);
  }
  .tagline-row {
    position: absolute;
    top: 150px;
    left: 24px;
    right: 24px;
    display: flex;
    align-items: center;
    gap: 10px;
  }
  .tagline-rule { flex: 0 0 60px; height: 1.5px; background: var(--orange); }
  .tagline {
    color: var(--orange);
    font-size: 14.5px;
    font-weight: 400;
    letter-spacing: 0.3px;
    white-space: nowrap;
  }
  .tagline-rule.end { flex: 1; }
  .service-list {
    position: absolute;
    top: 196px;
    left: 44px;
    list-style: none;
  }
  .service-list li {
    font-size: 15px;
    line-height: 22px;
    color: var(--black);
    display: flex;
    align-items: center;
    gap: 10px;
  }
  .service-list li::before {
    content: "";
    width: 8px; height: 8px;
    border-radius: 50%;
    background: var(--orange);
    flex: none;
  }

  /* back */
  .card-back .brand {
    position: absolute;
    top: 60px;
    left: 38px;
  }
  .company-name {
    position: absolute;
    top: 118px;
    left: 40px;
    font-size: 15px;
    font-weight: 500;
    letter-spacing: 0.4px;
    color: var(--black);
  }
  .faint-disc {
    position: absolute;
    top: 40px;
    left: 320px;
    width: 150px; height: 150px;
    border-radius: 50%;
    background: var(--orange);
    opacity: 0.06;
  }
  .contact-block {
    position: absolute;
    top: 36px;
    right: 34px;
    width: 210px;
  }
  .person-name {
    font-size: 21px;
    font-weight: 700;
    letter-spacing: 0.5px;
    line-height: 1.1;
  }
  .person-title {
    color: var(--orange);
    font-size: 13.5px;
    letter-spacing: 0.5px;
    margin-bottom: 8px;
  }
  .contact-list { list-style: none; }
  .contact-list li {
    display: flex;
    align-items: center;
    gap: 9px;
    font-size: 13px;
    line-height: 18px;
    color: var(--black);
  }
  .contact-list svg { width: 11px; height: 11px; flex: none; }
  .back-wave {
    position: absolute;
    inset: 0;
    width: 100%;
    height: 100%;
  }
  .address {
    position: absolute;
    left: 40px;
    bottom: 24px;
    color: var(--white);
    font-size: 13.5px;
    line-height: 18px;
    letter-spacing: 0.3px;
  }
  .uen {
    position: absolute;
    right: 34px;
    top: 196px;
    color: var(--white);
    font-size: 13.5px;
    letter-spacing: 0.3px;
  }
  .uen-label { color: var(--orange); font-weight: 500; }
</style>
</head>
<body>

<section class="card card-front" aria-label="Business card front">
  <div class="brand">
    <span class="brand-dot"></span>
    <span class="brand-name">ORVANE</span>
  </div>
  <div class="front-rule-top"></div>
  <div class="tagline-row">
    <span class="tagline-rule"></span>
    <span class="tagline">INDUSTRIAL NETWORKING AND COMPUTING SPECIALIST</span>
    <span class="tagline-rule end"></span>
  </div>
  <ul class="service-list">
    <li>Industrial Ethernet / Wireless / Cellular</li>
    <li>Industrial and Embedded Computing</li>
    <li>Serial / Fieldbus Connectivity</li>
    <li>IP Video Surveillance</li>
    <li>Remote Automation</li>
  </ul>
</section>

<section class="card card-back" aria-label="Business card back">
  <svg class="back-wave" viewBox="0 0 600 343" preserveAspectRatio="none" aria-hidden="true">
    <path d="M0,300 C90,220 200,195 330,188 C450,182 540,160 600,105 L600,119 C540,174 450,196 330,202 C200,209 90,236 0,316 Z" fill="#f37122"/>
    <path d="M0,316 C90,236 200,209 330,202 C450,196 540,174 600,119 L600,343 L0,343 Z" fill="#000000"/>
  </svg>
  <div class="faint-disc"></div>
  <div class="brand">
    <span class="brand-dot"></span>
    <span class="brand-name">ORVANE</span>
  </div>
  <p class="company-name">ORVANE ASIA PACIFIC PTE LTD</p>

  <div class="contact-block">
    <p class="person-name">DANIEL REYES</p>
    <p class="person-title">SALES MANAGER</p>
    <ul class="contact-list">
      <li>
        <svg viewBox="0 0 12 12"><rect x="3" y="0.8" width="6" height="10.4" rx="1.2" fill="none" stroke="#f37122" stroke-width="1.3"/><circle cx="6" cy="9.3" r="0.7" fill="#f37122"/></svg>
        +65 8123 4567
      </li>
      <li>
        <svg viewBox="0 0 12 12"><path d="M2.5 1 L4.5 1 L5.3 3.6 L4 4.6 C4.7 6.2 5.8 7.3 7.4 8 L8.4 6.7 L11 7.5 L11 9.5 C11 10.3 10.3 11 9.5 11 C5.3 10.6 1.4 6.7 1 2.5 C1 1.7 1.7 1 2.5 1 Z" fill="#f37122"/></svg>
        +65 6555 0140
      </li>
      <li>
        <svg viewBox="0 0 12 12"><rect x="3" y="1" width="6" height="4" fill="none" stroke="#f37122" stroke-width="1.2"/><rect x="1" y="5" width="10" height="5" rx="1" fill="#f37122"/><rect x="3.5" y="8" width="5" height="3" fill="#f37122"/></svg>
        +65 6555 0183
      </li>
      <li>
        <svg viewBox="0 0 12 12"><rect x="1" y="2.5" width="10" height="7" fill="none" stroke="#f37122" stroke-width="1.2"/><path d="M1 2.5 L6 6.5 L11 2.5" fill="none" stroke="#f37122" stroke-width="1.2"/></svg>
        sales@orvane.com.sg
      </li>
      <li>
        <svg viewBox="0 0 12 12"><circle cx="6" cy="6" r="5" fill="none" stroke="#f37122" stroke-width="1.2"/><ellipse cx="6" cy="6" rx="2.2" ry="5" fill="none" stroke="#f37122" stroke-width="1"/><path d="M1 6 H11" stroke="#f37122" stroke-width="1"/></svg>
        www.orvane.com.sg
      </li>
    </ul>
  </div>

  <p class="uen"><span class="uen-label">UEN No:</span> 200411357K</p>
  <address class="address" style="font-style:normal">
    24 Kallan Crescent Tech Hub #05-12<br>
    (Lobby B), Singapore 400218
  </address>
</section>

</body>
</html>
```